German Headhunter/ HR Consultancy needs Business Cards Design

We need a business Card Design for our Company in Stuttgart. We are specialized as Headhunter/ HR Consultancy in Placement of specialist and managers in permanent employment. Please refer to our business logo.

```html
<!DOCTYPE html>
<html lang="de">
<head>
<meta charset="utf-8">
<title>Vantera Personalberatung – Visitenkarte</title>
<link rel="stylesheet" href="https://fonts.googleapis.com/css2?family=Montserrat:wght@700&family=Arimo:wght@400;700&display=swap">
<style>
  :root {
    --brand-blue: #3a55a6;
    --card-white: #ffffff;
    --accent-grey: #8f9196;
    --ink: #1e1e22;
    --stage: #d3d3d3;
  }
  * { box-sizing: border-box; margin: 0; padding: 0; }
  html, body { width: 1200px; height: 800px; overflow: hidden; }
  body {
    background: var(--stage);
    font-family: "Arimo", Arial, sans-serif;
    display: flex;
    align-items: center;
    justify-content: center;
    gap: 40px;
  }
  .card {
    position: relative;
    width: 540px;
    height: 308px;
    border-radius: 18px;
    overflow: hidden;
    box-shadow: 0 10px 24px rgba(0,0,0,.25);
  }
  /* Front */
  .card--front { background: var(--card-white); }
  .front__band { position: absolute; inset: 0; }
  .front__block {
    position: absolute; top: 0; right: 26px;
    width: 74px; height: 62px;
    background: var(--accent-grey);
  }
  .front__identity { position: absolute; left: 34px; top: 58px; }
  .front__name {
    font-family: "Montserrat", Arial, sans-serif;
    font-weight: 700; font-size: 21px; letter-spacing: .5px;
    color: var(--brand-blue); text-transform: uppercase;
  }
  .front__role { font-size: 14px; color: var(--ink); margin-top: 2px; }
  .front__contacts {
    position: absolute; left: 34px; top: 140px;
    list-style: none; color: var(--card-white); font-size: 15px;
  }
  .front__contacts li { display: flex; align-items: center; gap: 8px; line-height: 22px; }
  .front__contacts svg { width: 13px; height: 13px; flex: none; }
  .front__address {
    position: absolute; left: 34px; top: 236px;
    font-size: 15px; line-height: 21px; color: var(--ink);
  }
  .front__brand {
    position: absolute; right: 36px; top: 128px;
    display: flex; align-items: center; gap: 10px;
    font-family: "Montserrat", Arial, sans-serif;
    font-weight: 700; font-size: 30px; color: var(--brand-blue);
  }
  .brand__square { width: 22px; height: 22px; background: currentColor; }
  /* Back */
  .card--back {
    background: var(--brand-blue);
    display: flex; align-items: center; justify-content: center;
  }
  .back__lockup {
    display: flex; align-items: center; gap: 16px;
    font-family: "Montserrat", Arial, sans-serif;
    font-weight: 700; color: var(--card-white);
  }
  .back__square { width: 46px; height: 46px; background: var(--card-white); }
  .back__name { font-size: 46px; line-height: 1; letter-spacing: 1px; }
  .back__descriptor { font-size: 17px; letter-spacing: 1px; margin-top: 4px; }
</style>
</head>
<body>
  <article class="card card--front" aria-label="Visitenkarte Vorderseite">
    <svg class="front__band" viewBox="0 0 540 308" aria-hidden="true">
      <polygon points="0,130 330,130 300,176 345,222 0,222" fill="var(--brand-blue)"/>
    </svg>
    <div class="front__block"></div>
    <div class="front__identity">
      <p class="front__name">Lukas Brenner</p>
      <p class="front__role">Managing Director</p>
    </div>
    <ul class="front__contacts">
      <li><svg viewBox="0 0 16 16"><path d="M4 1l3 3-2 2a9 9 0 005 5l2-2 3 3-2 3C7 15 1 9 1 3z" fill="currentColor"/></svg>0711-555 204 318</li>
      <li><svg viewBox="0 0 16 16"><rect x="1" y="3" width="14" height="10" fill="currentColor"/><path d="M1 3l7 6 7-6" stroke="var(--brand-blue)" stroke-width="1.4" fill="none"/></svg>kontakt@vantera-hr.de</li>
      <li><svg viewBox="0 0 16 16"><circle cx="8" cy="8" r="7" fill="currentColor"/><path d="M1 8h14M8 1v14M3 4h10M3 12h10" stroke="var(--brand-blue)" stroke-width="1" fill="none"/></svg>www.vantera-hr.de</li>
    </ul>
    <p class="front__address">18, Königstraße Süd<br>70173, Deutschland</p>
    <div class="front__brand"><span class="brand__square"></span>VANTERA</div>
  </article>

  <article class="card card--back" aria-label="Visitenkarte Rückseite">
    <div class="back__lockup">
      <span class="back__square"></span>
      <div>
        <p class="back__name">VANTERA</p>
        <p class="back__descriptor">PERSONALBERATUNG</p>
      </div>
    </div>
  </article>
</body>
</html>
```